Plumbing & Heating company

A leaflet containing -

Company name - Larkfield Plumbing Solutions
logo
Mobile number - 07700 914062
Landline - 01632 870215
Email - Info@larkfieldplumbing.example
website - Larkfield-plumbing.example
Social media logos - insta, Facebook

services we offer

- Boiler replacements (free quote)
- General plumbing & heating
- Tap replacements
- 1st & 2nd
- New builds & Extensions
- Cylinder replcemets

```html
<!DOCTYPE html>
<html lang="en">
<head>
<meta charset="utf-8">
<title>Larkfield Plumbing Solutions – Leaflet</title>
<link rel="stylesheet" href="https://fonts.googleapis.com/css2?family=Rubik:wght@700;800;900&family=Montserrat:wght@400;600;700&display=swap">
<style>
  :root{
    --blue:#1a75bb;
    --blue-dark:#0f5597;
    --blue-light:#2a9ee0;
    --red:#e3343a;
    --orange:#f08a24;
    --yellow:#f5b91f;
    --ink:#1d1d1f;
    --paper:#ffffff;
    --mist:#eef0f3;
    --stage:#e6e3de;
  }
  *{margin:0;padding:0;box-sizing:border-box}
  html,body{width:1200px;height:1200px;overflow:hidden;background:var(--stage)}
  .leaflet{
    position:absolute;left:197px;top:30px;width:806px;height:1140px;
    background:var(--paper);overflow:hidden;
    box-shadow:0 6px 24px rgba(0,0,0,.18);
    font-family:"Montserrat",sans-serif;color:var(--ink);
  }
  .artwork{position:absolute;inset:0;width:806px;height:1140px}
  .brand{position:absolute;left:48px;top:92px;display:flex;align-items:center;gap:14px}
  .brand-dot{width:58px;height:58px;border-radius:50%;background:var(--red)}
  .brand-name{
    font-family:"Rubik",sans-serif;font-weight:800;color:var(--blue);
    font-size:30px;line-height:1.02;text-transform:uppercase;letter-spacing:.5px;
  }
  .headline{
    position:absolute;left:44px;top:242px;
    font-family:"Rubik",sans-serif;font-weight:800;font-size:39px;line-height:1.02;
    text-transform:uppercase;
  }
  .headline .red{color:var(--red)}
  .headline .blue{color:var(--blue)}
  .coverage{position:absolute;left:44px;top:384px;font-size:20.5px;line-height:1.3}
  .coverage b{font-weight:700}
  .services-title{
    position:absolute;left:44px;top:462px;height:38px;width:310px;
  }
  .services-title span{
    position:absolute;left:8px;top:4px;font-family:"Rubik",sans-serif;font-weight:800;
    font-size:23px;color:#fff;letter-spacing:.3px;
  }
  .services{position:absolute;left:44px;top:524px;list-style:none}
  .services li{display:flex;align-items:center;height:62px;gap:14px;
    font-size:13.5px;font-weight:600;text-transform:uppercase;letter-spacing:.3px}
  .services svg{width:32px;height:32px;flex:none;fill:none;stroke:var(--blue);stroke-width:2;stroke-linecap:round;stroke-linejoin:round}
  .quote{position:absolute;left:52px;top:918px;color:#fff}
  .quote p{font-weight:700;font-size:18px;line-height:1.22;text-transform:uppercase;letter-spacing:.3px}
  .quote .mobile{font-family:"Rubik",sans-serif;font-weight:800;font-size:38px;letter-spacing:1px;margin-top:4px}
  .contacts{position:absolute;left:52px;top:1046px;list-style:none}
  .contacts li{display:flex;align-items:center;gap:8px;height:29px;font-size:16px}
  .contacts svg{width:20px;height:20px;flex:none}
</style>
</head>
<body>
<main class="leaflet">
  <svg class="artwork" viewBox="0 0 806 1140" aria-hidden="false">
    <defs>
      <linearGradient id="flameFill" x1="0" y1="0" x2="0" y2="1">
        <stop offset="0" stop-color="#e23a36"/>
        <stop offset=".55" stop-color="#ee7a2a"/>
        <stop offset="1" stop-color="#f5b322"/>
      </linearGradient>
      <linearGradient id="bandFill" x1="0" y1="0" x2="1" y2="0">
        <stop offset="0" stop-color="var(--blue-dark)"/>
        <stop offset="1" stop-color="var(--blue-light)"/>
      </linearGradient>
      <linearGradient id="unitFill" x1="0" y1="0" x2="1" y2="0">
        <stop offset="0" stop-color="#c9ced3"/>
        <stop offset=".5" stop-color="#f2f4f6"/>
        <stop offset="1" stop-color="#b9bfc5"/>
      </linearGradient>
    </defs>
    <path role="img" aria-label="Photo of a boiler room with blue pipework" fill="#2585c9"
      d="M400,0 H806 V520 L578,420 C572,250 520,90 400,0Z"/>
    <path role="img" aria-label="Photo of a red hot water cylinder" fill="#d8353a" stroke="#fff" stroke-width="6"
      d="M690,-5 H812 V920 H640 C590,820 566,620 600,525 C555,430 605,200 690,-5Z"/>
    <path role="img" aria-label="Flame shape with a cartoon plumber holding a wrench and plunger" fill="url(#flameFill)" stroke="#fff" stroke-width="6"
      d="M512,526 C470,620 405,720 398,860 C393,980 440,1070 482,1146 H812 V620 C720,660 560,640 512,526Z"/>
    <rect role="img" aria-label="Photo of a white wall-mounted combi boiler" x="606" y="490" width="174" height="250" fill="url(#unitFill)"/>
    <path fill="var(--mist)" d="M0,1025 H330 C400,1030 442,1080 494,1140 H0Z"/>
    <path fill="url(#bandFill)"
      d="M0,912 H290 C350,900 386,850 402,790 C398,920 432,1040 494,1140 C440,1080 400,1030 330,1025 H0Z"/>
  </svg>

  <div class="brand">
    <div class="brand-dot"></div>
    <div class="brand-name">Larkfield<br>Plumbing Solutions</div>
  </div>

  <h1 class="headline">
    <span class="red">Larkfield</span><br>
    <span class="blue">Plumbing &amp; Heating</span><br>
    <span class="red">Contractor</span>
  </h1>

  <p class="coverage">Based in <b>Hampshire</b> &amp; covering<br><b>Winchester</b> &amp; the surrounding areas</p>

  <div class="services-title">
    <svg width="310" height="38" viewBox="0 0 310 38">
      <polygon points="0,0 276,0 268,38 0,38" fill="var(--blue)"/>
      <polygon points="284,0 310,38 262,38" fill="var(--red)"/>
    </svg>
    <span>SERVICES WE OFFER</span>
  </div>

  <ul class="services">
    <li><svg viewBox="0 0 32 32"><rect x="3" y="6" width="11" height="18" rx="2"/><rect x="18" y="6" width="11" height="18" rx="2"/><path d="M6 24v4M11 24v4M21 24v4M26 24v4M6 12h5M21 12h5"/></svg>Boiler replacements</li>
    <li><svg viewBox="0 0 32 32"><path d="M4 5h10v12h12v10"/></svg>General plumbing &amp; heating</li>
    <li><svg viewBox="0 0 32 32"><path d="M4 14h14v8h8v-6h-8M11 14V8M7 8h8M26 22v4"/></svg>Tap replacements</li>
    <li><svg viewBox="0 0 32 32"><circle cx="14" cy="14" r="5"/><circle cx="14" cy="14" r="10" stroke-dasharray="4 3"/><circle cx="24" cy="24" r="6"/><path d="M21 24l2 2 4-4"/></svg>System design &amp; instlation 1st &amp; 2nd</li>
    <li><svg viewBox="0 0 32 32"><rect x="4" y="6" width="22" height="20" rx="1"/><path d="M4 12h22M12 12v14M4 20h8M20 4l8 8"/></svg>New builds &amp; extensions</li>
    <li><svg viewBox="0 0 32 32"><circle cx="16" cy="16" r="13"/><rect x="11" y="10" width="10" height="14" rx="4"/><path d="M14 7h4"/></svg>Cylinder replcemets</li>
  </ul>

  <div class="quote">
    <p>Get a free quote for<br>boiler replacement</p>
    <div class="mobile">07700 914062</div>
  </div>

  <ul class="contacts">
    <li><svg viewBox="0 0 20 20"><circle cx="10" cy="10" r="10" fill="var(--blue)"/><path d="M7 5l2 3-1 1.5c.6 1.3 1.5 2.2 2.5 2.5L12 11l3 2-1 2c-4 0-8-4-8-8z" fill="#fff"/></svg>01632 870215</li>
    <li><svg viewBox="0 0 20 20"><circle cx="10" cy="10" r="10" fill="var(--blue)"/><rect x="5" y="6.5" width="10" height="7" rx="1" fill="none" stroke="#fff" stroke-width="1.4"/><path d="M5.5 7l4.5 3.5L14.5 7" fill="none" stroke="#fff" stroke-width="1.4"/></svg>Info@larkfieldplumbing.example</li>
    <li><svg viewBox="0 0 20 20"><circle cx="10" cy="10" r="10" fill="var(--blue)"/><g fill="none" stroke="#fff" stroke-width="1.2"><circle cx="10" cy="10" r="5.5"/><ellipse cx="10" cy="10" rx="2.3" ry="5.5"/><path d="M4.5 10h11"/></g></svg>Larkfield-plumbing.example</li>
  </ul>
</main>
</body>
</html>
```